Redesign of business card for Cedar Ridge Mechanical

We are looking for a new design for our business cards for Cedar Ridge Mechanical. We are a plumbing & HVAC construction company, operating on the West Coast of Canada and USA. Logo attached.
Industry/Entity Type
Construction - Plumbing & HVAC
Contact Information for Business Card
Name, address, phone numbers, email, website address
Look and feel
Each slider illustrates characteristics of the customer's brand and the style your logo design should communicate.

```html
<!DOCTYPE html>
<html lang="en">
<head>
<meta charset="utf-8">
<title>Cedar Ridge Mechanical – Business Card</title>
<link rel="stylesheet" href="https://fonts.googleapis.com/css2?family=Roboto+Condensed:wght@700&family=Roboto:wght@400&display=swap">
<style>
  :root {
    --bg: #e4e4e4;
    --card-front: #f7f7f7;
    --card-back: #323232;
    --ink: #111111;
    --ink-soft: #555555;
    --band-dark: #000000;
    --band-grey: #767373;
    --white: #f5f5f5;
  }
  * { margin: 0; padding: 0; box-sizing: border-box; }
  html, body { width: 1200px; height: 1040px; overflow: hidden; background: var(--bg); }
  .canvas { position: relative; width: 1200px; height: 1040px; }

  .card {
    position: absolute;
    left: 280px;
    width: 640px;
    height: 366px;
    border-radius: 16px;
    overflow: hidden;
  }
  .card--front { top: 130px; background: var(--card-front); }
  .card--back  { top: 574px; background: var(--card-back); }

  .brand-name {
    position: absolute;
    right: 46px;
    top: 48px;
    display: flex;
    align-items: center;
    gap: 10px;
    font-family: "Roboto Condensed", Arial, sans-serif;
    font-weight: 700;
    font-size: 22px;
    line-height: 1.1;
    color: var(--ink);
    text-transform: uppercase;
    text-align: right;
  }
  .brand-name__mark { width: 14px; height: 14px; background: var(--ink); flex: none; }

  .person { position: absolute; left: 42px; top: 208px; }
  .person__name {
    font-family: "Roboto Condensed", Arial, sans-serif;
    font-weight: 700;
    font-size: 25px;
    color: var(--ink);
    line-height: 1.1;
  }
  .person__title {
    font-family: "Roboto", Arial, sans-serif;
    font-size: 16px;
    color: var(--ink-soft);
    margin-top: 2px;
  }

  .divider {
    position: absolute;
    left: 42px;
    width: 553px;
    top: 261px;
    height: 1px;
    background: var(--ink);
  }

  .contact {
    position: absolute;
    left: 42px;
    top: 272px;
    list-style: none;
    font-family: "Roboto", Arial, sans-serif;
    font-size: 15.5px;
    color: var(--ink);
  }
  .contact li { display: flex; align-items: center; gap: 7px; height: 20.5px; }
  .contact svg { width: 13px; height: 13px; fill: var(--ink); flex: none; }

  .address {
    position: absolute;
    right: 45px;
    top: 274px;
    font-family: "Roboto", Arial, sans-serif;
    font-style: normal;
    font-size: 15.5px;
    line-height: 20px;
    text-align: right;
    color: var(--ink);
  }

  .bands { position: absolute; left: 0; bottom: 0; width: 640px; height: 18px; }

  .back-name {
    position: absolute;
    left: 0; right: 0;
    top: 130px;
    display: flex;
    justify-content: center;
    align-items: center;
    gap: 16px;
    font-family: "Roboto Condensed", Arial, sans-serif;
    font-weight: 700;
    font-size: 40px;
    color: var(--white);
    text-transform: uppercase;
  }
  .back-name__mark { width: 26px; height: 26px; background: var(--white); }
  .back-web {
    position: absolute;
    left: 0; right: 0;
    top: 323px;
    text-align: center;
    font-family: "Roboto", Arial, sans-serif;
    font-size: 16px;
    color: var(--white);
  }
</style>
</head>
<body>
<main class="canvas">
  <section class="card card--front" aria-label="Card front">
    <div class="brand-name">
      <span class="brand-name__mark"></span>
      <span>Cedar Ridge<br>Mechanical</span>
    </div>

    <div class="person">
      <h1 class="person__name">Daniel Hughes</h1>
      <p class="person__title">President</p>
    </div>

    <div class="divider"></div>

    <ul class="contact">
      <li>
        <svg viewBox="0 0 24 24" aria-hidden="true"><path d="M6.6 10.8a15.1 15.1 0 0 0 6.6 6.6l2.2-2.2a1 1 0 0 1 1-.25 11.4 11.4 0 0 0 3.6.57 1 1 0 0 1 1 1V20a1 1 0 0 1-1 1A17 17 0 0 1 3 4a1 1 0 0 1 1-1h3.5a1 1 0 0 1 1 1c0 1.25.2 2.45.57 3.57a1 1 0 0 1-.25 1z"/></svg>
        (604) 555-0187
      </li>
      <li>
        <svg viewBox="0 0 24 24" aria-hidden="true"><path d="M2 5h20v14H2z M3.5 6.5 12 13l8.5-6.5" fill="none" stroke="#111" stroke-width="0"/><path d="M2 5h20v2l-10 7L2 7z"/><path d="M2 9l10 7 10-7v10H2z"/></svg>
        name@cedarridgemechanical.com
      </li>
      <li>
        <svg viewBox="0 0 24 24" aria-hidden="true"><circle cx="12" cy="12" r="10"/><path d="M8 6c2 1 1 3 3 4s0 4 2 5M15 5c-1 2 1 3 3 3" stroke="#f7f7f7" stroke-width="1.6" fill="none"/></svg>
        www.cedarridgemechanical.com
      </li>
    </ul>

    <address class="address">
      2170 Alder Grove Road<br>
      Coquitlam, BC V3K 2L5
    </address>

    <svg class="bands" viewBox="0 0 640 18" aria-hidden="true">
      <polygon points="0,0 419,0 414,18 0,18" fill="var(--band-dark)"/>
      <polygon points="423,0 640,0 640,18 418,18" fill="var(--band-grey)"/>
    </svg>
  </section>

  <section class="card card--back" aria-label="Card back">
    <div class="back-name">
      <span class="back-name__mark"></span>
      <span>Cedar Ridge Mechanical</span>
    </div>
    <p class="back-web">www.cedarridgemechanical.com</p>
  </section>
</main>
</body>
</html>
```